Realtor branding business card

modern, simple and self branding. Broker office logo needs to be used but not emphasized. Looking to brand myself

Target Market(s)

buyers, sellers and investors

Industry/Entity Type

Realtor

Contact Information for Business Card

Sample of my current business card on file

Requirements
Must have
• my website - tobiasmerrowkl.com
• Realtor logo
• Fair housing logo
Nice to have
• Colors from office logo but not a must
Should not have
• Do not want headshot

```html
<!DOCTYPE html>
<html lang="en">
<head>
<meta charset="utf-8">
<title>Tobias Merrow – Business Card</title>
<link href="https://fonts.googleapis.com/css2?family=Open+Sans:wght@400;700&display=swap" rel="stylesheet">
<style>
  :root{
    --backdrop:#d9d6d2;
    --card:#1f2022;
    --ink:#ffffff;
    --ink-soft:#e6e6e6;
    --rule:#bdbdbd;
  }
  *{margin:0;padding:0;box-sizing:border-box}
  html,body{width:1200px;height:864px;overflow:hidden}
  body{background:var(--backdrop);font-family:"Open Sans",sans-serif;position:relative}
  .card{position:absolute;width:630px;height:360px;background:var(--card);box-shadow:0 10px 30px rgba(0,0,0,.25);color:var(--ink);overflow:hidden}
  .card--front{left:60px;top:50px}
  .card--back{left:510px;top:454px}

  .brand{font-weight:700;color:var(--ink);white-space:nowrap;line-height:1.2}

  .card--front .brand{position:absolute;left:0;right:0;top:110px;text-align:center;font-size:30px}
  .front__badge-realtor{position:absolute;left:20px;top:188px;width:22px;height:24px;background:var(--ink-soft)}
  .front__rule{position:absolute;left:54px;right:54px;top:200px;height:1px;background:var(--rule)}
  .front__site{position:absolute;left:0;right:54px;top:232px;text-align:center;font-size:17px;letter-spacing:5px;color:var(--ink-soft)}
  .front__badge-housing{position:absolute;right:40px;bottom:34px;width:40px;height:40px;border:3px solid var(--ink-soft)}

  .card--back .brand{position:absolute;left:40px;top:164px;font-size:22px}
  .back__divider{position:absolute;left:338px;top:70px;width:1px;height:230px;background:linear-gradient(to bottom,transparent,var(--rule) 20%,var(--rule) 80%,transparent)}
  .contact{position:absolute;left:364px;top:76px;font-size:15px;line-height:1.3;color:var(--ink-soft)}
  .contact__name{font-weight:700;font-size:20px;color:var(--ink)}
  .contact__role{margin-bottom:8px}
  .contact__address{margin-bottom:10px}
  .contact__list{list-style:none}
  .contact__list li{display:flex;align-items:center;gap:8px;height:21px}
  .contact__list svg{width:14px;height:14px;fill:var(--ink);flex:none}
</style>
</head>
<body>

<section class="card card--front" aria-label="Card front">
  <p class="brand">Keystead Realty Group</p>
  <div class="front__badge-realtor" role="img" aria-label="Realtor membership badge"></div>
  <div class="front__rule"></div>
  <p class="front__site">www.tobiasmerrowkl.com</p>
  <div class="front__badge-housing" role="img" aria-label="Fair housing badge"></div>
</section>

<section class="card card--back" aria-label="Card back">
  <p class="brand">Keystead Realty Group</p>
  <div class="back__divider"></div>
  <div class="contact">
    <p class="contact__name">Tobias Merrow, PA</p>
    <p class="contact__role">Realtor</p>
    <p class="contact__address">482 Larkspur Vale Rd.<br>Corran Springs, FL 32790</p>
    <ul class="contact__list">
      <li><svg viewBox="0 0 16 16" aria-hidden="true"><path d="M3 1h3l1.5 4-2 1.3a9 9 0 0 0 4.2 4.2L11 8.5l4 1.5v3a2 2 0 0 1-2 2A13 13 0 0 1 1 3a2 2 0 0 1 2-2z"/></svg>407.555.0142</li>
      <li><svg viewBox="0 0 16 16" aria-hidden="true"><path d="M4 0h8a1 1 0 0 1 1 1v14a1 1 0 0 1-1 1H4a1 1 0 0 1-1-1V1a1 1 0 0 1 1-1zm1 2v10h6V2zm3 11a1 1 0 1 0 0 2 1 1 0 0 0 0-2z"/></svg>407.555.0187</li>
      <li><svg viewBox="0 0 16 16" aria-hidden="true"><path d="M0 3h16v10H0zm1.5 1.2V12h13V4.2L8 9z M2 4l6 4.2L14 4z"/></svg>merrowrealty@mailbox.com</li>
      <li><svg viewBox="0 0 16 16" aria-hidden="true"><path d="M8 0a8 8 0 1 0 0 16A8 8 0 0 0 8 0zm0 1.5c.9 0 2 1.8 2.3 4.5H5.7C6 3.3 7.1 1.5 8 1.5zM5.7 10h4.6c-.3 2.7-1.4 4.5-2.3 4.5S6 12.7 5.7 10zM1.6 7h2.6v2H1.6zm10.2 0h2.6v2h-2.6zM5.6 7h4.8v2H5.6z"/></svg>www.tobiasmerrowkl.com</li>
    </ul>
  </div>
</section>

</body>
</html>
```